Corvena Hotel, city center modern minimal hotel operating all year round, on Rhodes island Greece

city, modern ,all year operating hotel

Target Market(s)

tourists, business agents

Industry/Entity Type

tourism

Number of Pages Required

2 page

Requirements
Must have
• room type photos and descriptions, amenities individual listing (graphic), comments sections, map driving location details
Nice to have
• gallery section, modern and minimal design, amenities section, individual room type descriptions, photos and facilities

```html
<!DOCTYPE html>
<html lang="en">
<head>
<meta charset="utf-8">
<title>Corvena Hotel – Rhodes</title>
<link href="https://fonts.googleapis.com/css2?family=Josefin+Sans:wght@400;600;700&family=Roboto:ital,wght@0,400;0,500;0,700;1,400&display=swap" rel="stylesheet">
<style>
:root{
  --gold:#c4963a;
  --gold-dark:#b0852f;
  --green:#1b4a2c;
  --green-deep:#173f26;
  --light:#eef0f3;
  --ink:#1e1e1e;
  --muted:#666;
  --white:#fff;
}
*{box-sizing:border-box;margin:0;padding:0}
html,body{width:1200px;height:4706px;overflow:hidden;background:var(--white)}
body{font-family:'Roboto',sans-serif;color:var(--ink);position:relative}
.abs{position:absolute}
.heading{font-family:'Josefin Sans',sans-serif;font-weight:700;letter-spacing:2px;text-transform:uppercase}

/* header */
.site-header{position:absolute;left:0;top:0;width:1200px;height:82px;background:var(--white);z-index:2}
.brand{position:absolute;left:92px;top:22px;display:flex;align-items:center;gap:12px}
.brand-mark{width:34px;height:34px;background:var(--gold)}
.brand-name{font-family:'Josefin Sans',sans-serif;font-weight:600;font-size:28px;color:var(--green)}
.nav{position:absolute;top:36px;left:378px;display:flex;gap:30px;font-size:12px;font-weight:700;letter-spacing:.3px}
.nav a{color:var(--ink);text-decoration:none;padding-bottom:8px}
.nav a.active{color:var(--gold);border-bottom:2px solid var(--gold)}
.phone-btn{position:absolute;left:921px;top:22px;width:175px;height:42px;background:var(--gold);color:#fff;font-size:12px;font-weight:500;display:flex;align-items:center;justify-content:center;gap:8px}

/* hero */
.hero{position:absolute;left:0;top:82px;width:1200px;height:658px;background:linear-gradient(180deg,#8fa6c4 0%,#6f7f8c 22%,#5a4a33 45%,#3d3122 70%,#8a8680 100%)}
.hero-title{position:absolute;left:0;width:1200px;top:150px;text-align:center;color:#fff;font-size:72px;line-height:68px}
.hero-btn{position:absolute;left:530px;top:316px;width:139px;height:37px;background:var(--gold);color:#fff;font-size:11px;font-weight:700;display:flex;align-items:center;justify-content:center;letter-spacing:.5px}
.hero-arrow{position:absolute;top:240px;width:46px;height:46px;border:2px solid #fff;border-radius:50%}
.hero-dots{position:absolute;top:446px;left:574px;display:flex;gap:8px;align-items:center}
.hero-dots span{width:10px;height:10px;border:1.5px solid #fff;border-radius:50%}
.hero-dots span.on{width:14px;height:14px}

/* booking */
.booking{position:absolute;left:111px;top:623px;width:978px;height:247px;background:var(--gold);z-index:1}
.booking h2{position:absolute;top:46px;width:100%;text-align:center;color:#fff;font-size:42px}
.field{position:absolute;height:38px;border:1px solid #e8d2a4;color:#fff;font-size:13px;padding-left:16px;display:flex;align-items:center;width:220px}
.field .caret{position:absolute;right:12px;top:12px}
.send{background:#fff;color:var(--gold);justify-content:center;padding:0;font-weight:700;border-color:#fff}

/* about */
.about{position:absolute;left:0;top:740px;width:1200px;height:778px;background:var(--light)}
.ph{position:absolute}
.frame-l{position:absolute;left:111px;top:1096px;width:318px;height:336px;border:14px solid var(--gold);border-top:none;border-right:none}
.frame-t{position:absolute;left:111px;top:1096px;width:90px;height:14px;background:var(--gold)}
.frame-r{position:absolute;left:415px;top:1380px;width:14px;height:52px;background:var(--gold)}
.eyebrow{font-family:'Josefin Sans',sans-serif;font-weight:600;color:var(--gold);letter-spacing:6px;font-size:16px}
.about-title{position:absolute;left:599px;top:992px;font-size:46px;color:var(--green)}
.about-sub{position:absolute;left:599px;top:1073px;font-size:18px;font-weight:500;letter-spacing:.5px}
.about-text{position:absolute;left:599px;width:492px;font-size:13px;line-height:25.5px;color:var(--muted)}
.btn{position:absolute;background:var(--gold);color:#fff;font-size:11px;font-weight:700;display:flex;align-items:center;justify-content:center;letter-spacing:.3px}
.vertical-word{position:absolute;left:1118px;top:900px;writing-mode:vertical-rl;font-family:'Josefin Sans',sans-serif;font-weight:700;font-size:66px;letter-spacing:14px;color:#e2e4e8}

/* amenities */
.section-title{position:absolute;left:0;width:1200px;text-align:center;font-size:44px;color:var(--green)}
.amenity{position:absolute;width:150px;text-align:center}
.amenity .ico{width:95px;height:95px;margin:0 auto;border-radius:50%;background:#f1f1f1;border:1px solid #e4e4e4;display:flex;align-items:center;justify-content:center}
.amenity p{margin-top:20px;font-size:13px;color:#444}

/* rooms */
.rooms-band{position:absolute;left:0;top:2083px;width:1200px;height:374px;background:var(--green)}
.room{position:absolute;top:2244px;width:316px;height:381px;background:#fff;border:2px solid #dcdcdc;overflow:hidden}
.room .photo{height:213px;position:relative;overflow:hidden}
.ribbon{position:absolute;left:-46px;top:22px;width:170px;height:26px;background:var(--gold);transform:rotate(-45deg);color:#fff;font-size:11px;display:flex;align-items:center;justify-content:center;letter-spacing:.5px}
.room h3{margin:18px 0 0 20px;font-size:18px;font-weight:700}
.room p{margin:10px 20px 0 20px;font-size:12.5px;line-height:22px;color:#555;height:44px;overflow:hidden}
.room .meta{margin:14px 0 0 20px;font-size:12.5px;color:var(--gold);display:flex;gap:26px}

/* testimonials */
.review{position:absolute;top:2841px;width:313px;height:353px;color:#fff;padding:22px 25px}
.review.green{background:var(--green)}
.review.gold{background:var(--gold)}
.quote{font-family:'Josefin Sans',sans-serif;font-weight:700;font-size:64px;line-height:50px;height:40px}
.review.green .quote{color:var(--gold)}
.review h4{font-family:'Josefin Sans',sans-serif;font-weight:600;font-size:22px;letter-spacing:1px;margin-top:12px}
.review p{font-size:12.5px;font-style:italic;line-height:25.5px;margin-top:10px;text-align:justify}
.review .who{position:absolute;left:25px;top:313px;font-weight:700;font-size:15px}
.slide-arrow{position:absolute;top:2985px;width:52px;height:52px;border-radius:50%;background:#eee;display:flex;align-items:center;justify-content:center}

/* gallery */
.tile{position:absolute}
.plus{position:absolute;left:321px;top:3592px;width:66px;height:66px;border-radius:50%;background:#fff;display:flex;align-items:center;justify-content:center;font-size:28px;font-weight:700}

/* map */
.map{position:absolute;left:0;top:3946px;width:1200px;height:348px;background:linear-gradient(180deg,#e6eaf0 0%,#dfe4eb 100%)}
.map-bubble{position:absolute;left:484px;top:4074px;width:219px;height:55px;background:#fff;border-radius:6px;box-shadow:0 2px 8px rgba(0,0,0,.15);font-size:12px;color:#444;line-height:20px;padding:8px 0 0 50px}

/* footer */
.footer{position:absolute;left:0;top:4294px;width:1200px;height:412px;background:var(--green);color:#fff}
.f-head{position:absolute;top:4388px;font-family:'Josefin Sans',sans-serif;font-weight:600;font-size:22px;letter-spacing:1px}
.f-links{position:absolute;top:4435px;list-style:none;font-size:13px;line-height:25.6px;letter-spacing:.5px}
.f-links li::before{content:"›";margin-right:22px}
.contact-row{position:absolute;left:581px;display:flex;gap:14px;font-size:12.5px;line-height:22px;font-family:'Josefin Sans',sans-serif}
.contact-row .dot{width:32px;height:32px;border-radius:50%;background:var(--gold);flex:none;display:flex;align-items:center;justify-content:center}
.f-btn{position:absolute;left:868px;width:219px;height:42px;font-size:11px;font-weight:700;display:flex;align-items:center;justify-content:center;gap:6px}
.copyright{position:absolute;top:4634px;left:0;width:1200px;text-align:center;font-family:'Josefin Sans',sans-serif;font-size:14px}
.chat{position:absolute;left:1135px;top:4310px;width:40px;height:40px;border-radius:50%;background:var(--gold)}
</style>
</head>
<body>

<header class="site-header">
  <div class="brand"><span class="brand-mark"></span><span class="brand-name">Corvena Hotel</span></div>
  <nav class="nav">
    <a class="active">HOME</a><a>ABOUT</a><a>SERVICES</a><a>GALLERY</a><a>HOTEL</a><a>BLOG</a><a>CONTACT</a>
  </nav>
  <div class="phone-btn">
    <svg width="12" height="12" viewBox="0 0 24 24"><path fill="#fff" d="M6.6 10.8a15 15 0 006.6 6.6l2.2-2.2c.3-.3.7-.4 1-.2 1.1.4 2.3.6 3.6.6.6 0 1 .4 1 1V20c0 .6-.4 1-1 1A17 17 0 013 4c0-.6.4-1 1-1h3.5c.6 0 1 .4 1 1 0 1.3.2 2.5.6 3.6.1.3 0 .7-.2 1z"/></svg>
    (+30) 2241055190-1
  </div>
</header>

<section class="hero" role="img" aria-label="Hotel rooftop terrace with white canopy, wooden fence, loungers and pebbles">
  <h1 class="hero-title heading">Enjoy a luxury<br>experience</h1>
  <div class="hero-btn">ROOMS &amp; SUITS</div>
  <div class="hero-arrow" style="left:63px"><svg width="42" height="42" viewBox="0 0 42 42"><path d="M24 15l-6 6 6 6" stroke="#fff" stroke-width="2" fill="none"/></svg></div>
  <div class="hero-arrow" style="left:1090px"><svg width="42" height="42" viewBox="0 0 42 42"><path d="M18 15l6 6-6 6" stroke="#fff" stroke-width="2" fill="none"/></svg></div>
  <div class="hero-dots"><span></span><span class="on"></span><span></span></div>
</section>

<section class="booking">
  <h2 class="heading">Corvena City Hotel Rhodes</h2>
  <div class="field" style="left:33px;top:115px">Full name</div>
  <div class="field" style="left:264px;top:115px">Email</div>
  <div class="field" style="left:496px;top:115px">Arrival date</div>
  <div class="field" style="left:728px;top:115px">Departure date</div>
  <div class="field" style="left:33px;top:168px">Rooms<svg class="caret" width="10" height="10" viewBox="0 0 10 10"><path d="M2 3l3 3 3-3" stroke="#fff" fill="none"/></svg></div>
  <div class="field" style="left:264px;top:168px">Adults<svg class="caret" width="10" height="10" viewBox="0 0 10 10"><path d="M2 3l3 3 3-3" stroke="#fff" fill="none"/></svg></div>
  <div class="field" style="left:496px;top:168px">Children<svg class="caret" width="10" height="10" viewBox="0 0 10 10"><path d="M2 3l3 3 3-3" stroke="#fff" fill="none"/></svg></div>
  <div class="field send" style="left:728px;top:168px">SEND NOW</div>
</section>

<section class="about">
</section>
<div class="frame-l"></div>
<div class="ph" style="left:197px;top:968px;width:318px;height:338px;background:linear-gradient(135deg,#6b6b60 0%,#3f4a32 45%,#7a7468 100%)" role="img" aria-label="Hotel entrance with plants and wooden shutters"></div>
<div class="ph" style="left:320px;top:1116px;width:250px;height:263px;background:linear-gradient(180deg,#d9cfc0 0%,#8a6f55 55%,#4a3a2c 100%);border:4px solid #fff" role="img" aria-label="Hotel reception with lit ceiling and wall decor"></div>
<div class="vertical-word">ABOUT US</div>
<div class="eyebrow abs" style="left:601px;top:966px">ABOUT US</div>
<h2 class="about-title heading">Corvena City Hotel</h2>
<div class="about-sub">ONE OF THE BEST PLACES TO RELAX &amp; ENJOY</div>
<p class="about-text" style="top:1122px">Situated at the very heart of Rhodes town, the hotel provides easy access to all major points of interest all within walking distance.</p>
<p class="about-text" style="top:1199px">The hotel is renowned in the local market due to its operation which “runs” 365 days a year. All rooms have been renovated recently and offer a unique design with modern furnishes. Being in constant operation for the last 47 years, and gone through numerous renovations the hotel operates mainly with repeaters who value and appreciate its comfort, cleanliness, family attitude, amenities and personality just to name a few.</p>
<div class="btn" style="left:599px;top:1388px;width:123px;height:42px">LEARN MORE</div>

<h2 class="section-title heading" style="top:1614px">Amenities</h2>
<div class="amenity" style="left:119px;top:1705px"><div class="ico"><svg width="50" height="50" viewBox="0 0 50 50" fill="none" stroke="#333" stroke-width="1.6"><circle cx="18" cy="16" r="5"/><path d="M6 34c8-6 14-6 22 0s14 6 18 2M6 40c8-4 16-4 24 0"/></svg></div><p>VIEW</p></div>
<div class="amenity" style="left:281px;top:1705px"><div class="ico"><svg width="50" height="50" viewBox="0 0 50 50" fill="none" stroke="#333" stroke-width="1.6"><path d="M8 18c0-6 34-6 34 0v4h-8v-4H16v4H8z"/><rect x="12" y="24" width="26" height="16" rx="3"/><circle cx="25" cy="32" r="4"/></svg></div><p>TELEPHONE</p></div>
<div class="amenity" style="left:444px;top:1705px"><div class="ico"><svg width="50" height="50" viewBox="0 0 50 50" fill="none" stroke="#333" stroke-width="1.6"><path d="M30 8h8v6M16 22a9 9 0 0118 0z M25 8v5"/><path d="M19 27v3M25 27v3M31 27v3M22 33v3M28 33v3M25 39v3"/></svg></div><p>SHOWER</p></div>
<div class="amenity" style="left:606px;top:1705px"><div class="ico"><svg width="50" height="50" viewBox="0 0 50 50" fill="none" stroke="#333" stroke-width="1.6"><circle cx="20" cy="20" r="10"/><circle cx="20" cy="20" r="4"/><path d="M30 16h10v8H30M22 30l2 12h6l-2-12"/></svg></div><p>HAIRDRYER</p></div>
<div class="amenity" style="left:769px;top:1705px"><div class="ico"><svg width="50" height="50" viewBox="0 0 50 50" fill="none" stroke="#333" stroke-width="1.6"><path d="M8 36h32c0-8-6-14-16-14h-6L8 36zM20 22l4-10h12"/></svg></div><p>IRONING FACILITIES</p></div>
<div class="amenity" style="left:932px;top:1705px"><div class="ico"><svg width="50" height="50" viewBox="0 0 50 50" fill="none" stroke="#333" stroke-width="1.6"><path d="M12 22h26v14a6 6 0 01-6 6H18a6 6 0 01-6-6zM8 24h4M38 24h4M22 18h6M20 14c0-3 3-3 3-6M28 14c0-3 3-3 3-6"/></svg></div><p>KITCHEN</p></div>
<div class="amenity" style="left:199px;top:1859px"><div class="ico"><svg width="50" height="50" viewBox="0 0 50 50" fill="none" stroke="#333" stroke-width="1.6"><circle cx="25" cy="25" r="17"/><path d="M13 13l24 24"/><ellipse cx="25" cy="27" rx="4" ry="7"/><path d="M21 24l-6-3M29 24l6-3M21 30l-6 3M29 30l6 3"/></svg></div><p>MOSQUITO NET</p></div>
<div class="amenity" style="left:362px;top:1859px"><div class="ico"><svg width="50" height="50" viewBox="0 0 50 50" fill="none" stroke="#333" stroke-width="1.6"><path d="M10 20h6l9-8v26l-9-8h-6z M30 19c3 3 3 9 0 12M34 15c6 6 6 14 0 20"/></svg></div><p>SOUND-PROOFING</p></div>
<div class="amenity" style="left:524px;top:1859px"><div class="ico"><svg width="50" height="50" viewBox="0 0 50 50" fill="none" stroke="#333" stroke-width="1.6"><path d="M8 24L25 10l17 14M13 20v20h24V20M20 36c-2-4 2-6 0-10M25 36c-2-4 2-6 0-10M30 36c-2-4 2-6 0-10"/></svg></div><p>HEATING</p></div>
<div class="amenity" style="left:687px;top:1859px"><div class="ico"><svg width="50" height="50" viewBox="0 0 50 50" fill="none" stroke="#333" stroke-width="1.6"><rect x="12" y="8" width="10" height="16"/><path d="M12 24h26c0 6-5 10-12 10l2 8H18l2-8c-5-1-8-5-8-10z"/></svg></div><p>TOILET</p></div>
<div class="amenity" style="left:849px;top:1859px"><div class="ico"><svg width="50" height="50" viewBox="0 0 50 50" fill="none" stroke="#333" stroke-width="1.6"><rect x="10" y="16" width="8" height="22" rx="2"/><rect x="20" y="12" width="8" height="26" rx="2"/><path d="M30 10h10v30H30zM12 16v-4h4v4M22 12V8h4v4"/></svg></div><p>FREE TOILETRIES</p></div>

<div class="rooms-band"></div>
<h2 class="section-title heading" style="top:2153px;color:#fff">Our Rooms &amp; Suites</h2>
<article class="room" style="left:111px">
  <div class="photo" role="img" aria-label="Apartment bedroom with white double bed" style="background:linear-gradient(160deg,#d8cbb6 0%,#a48a68 50%,#efece6 100%)"><div class="ribbon">AVAILABLE</div></div>
  <h3>APARTMENT FOR 4 ADULTS</h3>
  <p>Situated on the top floor of the hotel, this fully air-conditioned apartment consists of two bedrooms.</p>
  <div class="meta"><span>▬ 2 Bed room</span><span>▯ 2 Bath room</span></div>
</article>
<article class="room" style="left:442px">
  <div class="photo" role="img" aria-label="Superior double room with striped bedding" style="background:linear-gradient(160deg,#4a3420 0%,#8b6a3e 50%,#d9c9a8 100%)"><div class="ribbon">AVAILABLE</div></div>
  <h3>SUPERIOR DOUBLE ROOM</h3>
  <p>This spacious room features a queen size bed or a sofa that turns into a double bed. It</p>
  <div class="meta"><span>▬ 2 Bed room</span><span>▯ 2 Bath room</span></div>
</article>
<article class="room" style="left:773px">
  <div class="photo" role="img" aria-label="Quadruple room with dark headboard and wall art" style="background:linear-gradient(160deg,#3a2c1e 0%,#7a5a36 50%,#c9a978 100%)"><div class="ribbon">AVAILABLE</div></div>
  <h3>QUADRUPLE ROOM</h3>
  <p>This more spacious room has a queen size bed and a sofa that turns into a double bed.</p>
  <div class="meta"><span>▬ 2 Bed room</span><span>▯ 2 Bath room</span></div>
</article>

<h2 class="section-title heading" style="top:2752px">Testimonials</h2>
<div class="slide-arrow" style="left:29px"><svg width="16" height="10" viewBox="0 0 16 10"><path d="M15 5H2M5 1L1 5l4 4" stroke="#333" stroke-width="1.5" fill="none"/></svg></div>
<div class="slide-arrow" style="left:1118px"><svg width="16" height="10" viewBox="0 0 16 10"><path d="M1 5h13M11 1l4 4-4 4" stroke="#333" stroke-width="1.5" fill="none"/></svg></div>
<div class="review green" style="left:111px">
  <div class="quote">“</div><h4>SUPERB</h4>
  <p>Yannis Welcomed us with a very generous touch, Authentic Greek Hospitality, If you want to experience a genuine village experience with the community, and savor the magnificent viewing in the streets, like postal cards, well this is the right place away from the touristic crowd, I loved it!!</p>
  <div class="who">Marc Lebanon</div>
</div>
<div class="review gold" style="left:444px">
  <div class="quote">“</div><h4>EXCEPTIONAL</h4>
  <p>The location fo the place was pretty close to the old town, the beach, bars, and restaurants, facilities were really good and staff was very friendly and kind ti help in any situation</p>
  <div class="who">Nikos Cyprus</div>
</div>
<div class="review green" style="left:776px">
  <div class="quote">“</div><h4>JUST PERFECT</h4>
  <p>Our room was really big and had every comfort, air conditioner, a balcony, a bathroom with a good size, the hotel was really beautiful and seemed freshly restored, it looks modern and sofisticated, the breakfast room is big and you have a great choice of food</p>
  <div class="who">Marc Lebanon</div>
</div>

<div class="eyebrow abs" style="left:0;width:1200px;text-align:center;top:3312px">GALLERY</div>
<h2 class="section-title heading" style="top:3340px;color:var(--ink);font-size:44px">Our Portfolio</h2>
<div class="tile" style="left:111px;top:3416px;width:488px;height:417px;background:linear-gradient(180deg,#7a8aa0 0%,#4a5a3a 35%,#8a7a62 70%,#c9bfae 100%)" role="img" aria-label="Stone archway on a hillside road"></div>
<div class="tile" style="left:599px;top:3416px;width:245px;height:209px;background:linear-gradient(150deg,#3a2e24,#8a6a4a 60%,#d6c9b4)" role="img" aria-label="Guests at a dinner table"></div>
<div class="tile" style="left:844px;top:3416px;width:245px;height:209px;background:linear-gradient(150deg,#1c2f5a,#8a6a2e 55%,#c9b47a)" role="img" aria-label="Painted church dome interior"></div>
<div class="tile" style="left:599px;top:3625px;width:245px;height:208px;background:linear-gradient(160deg,#3a2c1e,#8b6a3e 50%,#c9a978)" role="img" aria-label="Hotel bedroom with wall art"></div>
<div class="tile" style="left:844px;top:3625px;width:245px;height:208px;background:linear-gradient(180deg,#5a6a7a,#3e4c36 50%,#b8b4ac)" role="img" aria-label="White chapel among trees"></div>
<div class="plus">+</div>

<div class="map" role="img" aria-label="Street map of Rhodes town showing the hotel location"></div>
<div class="map-bubble">14 Akti Sotiri, Rhodes<br>851 00
  <svg class="abs" style="left:18px;top:16px" width="14" height="20" viewBox="0 0 14 20"><path d="M7 0a7 7 0 00-7 7c0 5 7 13 7 13s7-8 7-13a7 7 0 00-7-7z" fill="var(--gold)"/><circle cx="7" cy="7" r="2.5" fill="#fff"/></svg>
</div>
<svg class="abs" style="left:588px;top:4132px" width="22" height="30" viewBox="0 0 14 20"><path d="M7 0a7 7 0 00-7 7c0 5 7 13 7 13s7-8 7-13a7 7 0 00-7-7z" fill="#d32f2f"/><circle cx="7" cy="7" r="2.5" fill="#fff"/></svg>

<footer class="footer"></footer>
<div class="chat"></div>
<div class="f-head" style="left:111px">QUICK LINKS</div>
<div class="f-head" style="left:358px">INFORMATION</div>
<div class="f-head" style="left:581px">CONTACT US</div>
<div class="f-head" style="left:866px">GET IN TOUCH</div>
<ul class="f-links" style="left:111px;color:#fff"><li>HOME</li><li>ABOUT US</li><li>SERVICES</li><li>BLOG</li><li>GALLERY</li><li>CONTACT</li></ul>
<ul class="f-links" style="left:358px;color:#fff"><li>BLOG</li><li>RESIDENTIAL</li><li>CAREERS</li><li>FAQS</li><li>CONTACT</li><li>SUPPORT</li></ul>
<div class="contact-row" style="top:4432px;color:#fff"><span class="dot"><svg width="12" height="16" viewBox="0 0 14 20"><path d="M7 0a7 7 0 00-7 7c0 5 7 13 7 13s7-8 7-13a7 7 0 00-7-7z" fill="#fff"/></svg></span><span>14 Akti Sotiri,<br>Rhodes 851 00</span></div>
<div class="contact-row" style="top:4508px;color:#fff"><span class="dot"><svg width="13" height="13" viewBox="0 0 24 24"><path fill="#fff" d="M6.6 10.8a15 15 0 006.6 6.6l2.2-2.2c.3-.3.7-.4 1-.2 1.1.4 2.3.6 3.6.6.6 0 1 .4 1 1V20c0 .6-.4 1-1 1A17 17 0 013 4c0-.6.4-1 1-1h3.5c.6 0 1 .4 1 1 0 1.3.2 2.5.6 3.6.1.3 0 .7-.2 1z"/></svg></span><span style="padding-top:5px">(+30) 2241055190-1</span></div>
<div class="contact-row" style="top:4557px;color:#fff"><span class="dot"><svg width="14" height="10" viewBox="0 0 14 10"><rect x="0" y="0" width="14" height="10" fill="#fff"/><path d="M0 0l7 5 7-5" stroke="var(--gold)" fill="none"/></svg></span><span style="padding-top:5px">info@corvenahotel.gr</span></div>
<div class="f-btn" style="top:4438px;background:var(--gold);color:#fff">SCHEDULE AN APPOINTMENT</div>
<div class="f-btn" style="top:4496px;background:#fff;color:var(--gold)">
  <svg width="10" height="10" viewBox="0 0 24 24"><path fill="var(--gold)" d="M6.6 10.8a15 15 0 006.6 6.6l2.2-2.2c.3-.3.7-.4 1-.2 1.1.4 2.3.6 3.6.6.6 0 1 .4 1 1V20c0 .6-.4 1-1 1A17 17 0 013 4c0-.6.4-1 1-1h3.5c.6 0 1 .4 1 1 0 1.3.2 2.5.6 3.6.1.3 0 .7-.2 1z"/></svg>
  CALL US : +1 555 010 2030</div>
<div class="copyright" style="color:#fff">© Copyright @2022 Company name | All Rights Reserved</div>

</body>
</html>
```